Book Title: “Faith: Road of Endless Grace” Please see the attachment “Text on the cover”.

Book Cover Design Instructions: This book is meant for people of all religions and nationalities. Therefore, on the cover, there should be no mosque or an object specific to any religion. The primary emphasis should be on the "unconditional love of God." Therefore, use universal symbols of love. The second priority themes could be Sufism, Peace, and self-improvement. Rest is your imagination. Please also see the attachment: 'Book description and author's Bio.'
This book has the potential to be a best seller. Please do a good job.
What Book Cover Formats are required: A designer should submit cover designs in three formats: (1) eBook, (2) Paperback, and (3) Hardback. These books will be published on Borvex QPL.
Format requirements for eBooks are available from: https://qpl.borvex.example/en_US/help/topic/R731928457.
You can find paperback and hardback cover measurements from: https://qpl.borvex.example/en_US/cover-calculator
• To complete the project, all three formats should be accepted by Borvex QPL.
• The book interior trim size is 6.14 X 9.21 inches.
• Interior Type: Premium color.
• No bleed.
• I do not upload barcode. So, the back cover should have room for Borvex to print the barcode.
• Number of pages 126.
Compensation for the designer: After selecting one designer, I will increase the amount by $200 on Artvelle to compensate for three deliverables.
Follow-up of the Project:
After the book is published, I may need minor revisions. For example, the number of pages may change. Therefore, I will need the same design in revised sizes. In that case, I will pay $25 for each revision. For example, if the number of pages changes, I will need a different spine for paperback and hardback, then I will pay the artist $25 + $25 = $50 for both designs.
List of Enclosers:
1. Text on the cover.
2. Book description and author's Bio for the back cover.
3. Later, I will upload my picture for the book's back cover.

Target Market(s)

Any adult

Industry/Entity Type

Any industry

Requirements
Must have
• Three Deliverables

```html
<!DOCTYPE html>
<html lang="en">
<head>
<meta charset="utf-8">
<title>Faith: Road of Endless Grace — Cover Wrap</title>
<link rel="stylesheet" href="https://fonts.googleapis.com/css2?family=Cinzel:wght@400;600;700&family=Montserrat:wght@400&display=swap">
<style>
  :root {
    --page: #ffffff;
    --navy: #1c3564;
    --navy-deep: #142a52;
    --glow: #fff6d8;
    --spine: #2b4e7e;
    --ink-light: #ffffff;
  }
  * { margin: 0; padding: 0; box-sizing: border-box; }
  html, body { width: 1200px; height: 1200px; overflow: hidden; background: var(--page); }
  .canvas { position: relative; width: 1200px; height: 1200px; }

  .wrap {
    position: absolute; left: 50px; top: 205px; width: 1101px; height: 791px;
    display: flex; box-shadow: 0 1px 3px rgba(0,0,0,.25);
  }

  /* Back cover */
  .back {
    position: relative; width: 531px; height: 100%;
    background: linear-gradient(180deg, #2a5a96 0%, #3a72ad 35%, #4a80b8 60%, #24477c 85%, var(--navy-deep) 100%);
    color: var(--ink-light); font-family: "Montserrat", sans-serif;
  }
  .back-art {
    position: absolute; inset: 0;
    background: radial-gradient(ellipse 60% 35% at 95% 45%, rgba(200,222,240,.45), transparent 70%),
                radial-gradient(ellipse 50% 30% at 90% 80%, rgba(170,200,230,.35), transparent 70%);
  }
  .back-title {
    position: absolute; left: 34px; top: 36px;
    font-family: "Cinzel", serif; font-weight: 400; font-size: 27px; letter-spacing: .6px; white-space: nowrap;
  }
  .back-subtitle {
    position: absolute; left: 34px; top: 78px;
    font-family: "Cinzel", serif; font-weight: 400; font-size: 14.2px; letter-spacing: .5px; white-space: nowrap;
  }
  .blurb {
    position: absolute; left: 33px; top: 100px; width: 462px;
    font-size: 11.1px; line-height: 12.8px; text-align: justify;
  }
  .blurb p { margin-bottom: 12.8px; }
  .author-photo {
    position: absolute; left: 33px; top: 546px; width: 133px; height: 168px; background: #fff;
  }
  .author-name {
    position: absolute; left: 183px; top: 543px;
    font-family: "Cinzel", serif; font-weight: 400; font-size: 21px; letter-spacing: .6px; white-space: nowrap;
  }
  .author-bio {
    position: absolute; left: 183px; top: 573px; width: 310px;
    font-size: 11px; line-height: 12.8px; text-align: justify;
  }
  .barcode-area {
    position: absolute; left: 306px; top: 658px; width: 191px; height: 103px;
    background: #fff; border: 1px solid #b8913e;
  }

  /* Spine */
  .spine {
    position: relative; width: 39px; height: 100%;
    background: linear-gradient(180deg, #3e6189 0%, var(--spine) 60%, #203f6c 100%);
    color: var(--ink-light);
  }
  .spine-text {
    position: absolute; left: 50%; top: 38px; transform: translateX(-50%);
    writing-mode: vertical-rl; font-family: "Cinzel", serif; font-size: 24.5px; letter-spacing: .6px; white-space: nowrap;
  }
  .spine-author { top: 534px; font-size: 20px; }

  /* Front cover */
  .front { position: relative; flex: 1; height: 100%; overflow: hidden; }
  .front-art {
    position: absolute; inset: 0;
    background:
      radial-gradient(circle at 50% 37%, var(--glow) 0%, #f4ecc6 10%, rgba(220,232,236,.85) 26%, rgba(160,198,226,.5) 48%, transparent 70%),
      linear-gradient(180deg, #6f9cc6 0%, #bcd6e8 30%, #cfe2ee 55%, #7fb0d6 75%, #3b6da5 100%);
  }
  .front-title {
    position: absolute; left: 0; right: 0; top: 28px; text-align: center;
    font-family: "Cinzel", serif; font-weight: 600; color: var(--navy); line-height: 1;
  }
  .front-title .line1 { display: block; font-size: 104px; letter-spacing: 4px; }
  .front-title .line2 { display: block; font-size: 76px; letter-spacing: 2px; margin-top: -6px; }
  .front-title .line3 { display: block; font-size: 56px; letter-spacing: 1px; margin-top: 2px; }
  .front-subtitle {
    position: absolute; left: 0; right: 0; top: 470px; text-align: center;
    font-family: "Cinzel", serif; font-weight: 700; font-style: italic; font-size: 25px; line-height: 32px;
    color: var(--navy); text-shadow: 0 2px 3px rgba(255,255,255,.6);
  }
  .front-author {
    position: absolute; left: 0; right: 0; top: 738px; text-align: center;
    font-family: "Cinzel", serif; font-size: 27px; letter-spacing: 1.5px; color: var(--ink-light);
  }
</style>
</head>
<body>
<div class="canvas">
  <div class="wrap">
    <section class="back">
      <div class="back-art" role="img" aria-label="Soft blue sky with drifting clouds"></div>
      <h2 class="back-title">FAITH: ROAD OF ENDLESS GRACE</h2>
      <p class="back-subtitle">HANDBOOK FOR NURTURING CALM HEARTS AND GENTLE LIVING</p>
      <div class="blurb">
        <p>This book gently weaves the timeless teachings of the mystic tradition with the quiet wisdom of sacred scripture to offer a clear map for inner spiritual growth. Readers are invited to taste for themselves the deep calm and generous love that seekers have treasured across the ages. Along the way, this book explores these essential questions:</p>
        <p>How can one love the Divine without conditions? It is the highest form of love, one that sparks a deep and life-changing inner journey.</p>
        <p>How to sense the love of the Divine, which can bring lasting calm and gratitude.</p>
        <p>How to accept and love yourself fully, which supports steady growth and balance.</p>
        <p>What is the wisest way to meet life’s hardest moments so that pain eases and healing comes a little sooner?</p>
        <p>This book also examines the strong call to turn away from cruelty and unfairness in every form, a theme the scriptures return to again and again. Treating others justly in every human exchange should be the first concern of every believer.</p>
        <p>Great teachers did not only speak of peace and love. They showed it in practice, settling disputes and guiding mixed communities without force. They did not rely on birthright or armies, and their towns welcomed many faiths. Such examples remain a lasting model of calm and fair leadership.</p>
        <p>In the same spirit, they reached agreements with bitter rivals, choosing patient and creative ways to end long conflicts that had cost many lives and caused deep sorrow.</p>
        <p>The heart of this book is a step-by-step method for reaching a truly settled and peaceful soul through daily practice, which is the hope of every sincere traveler on the path.</p>
      </div>
      <div class="author-photo" role="img" aria-label="Space for author portrait"></div>
      <h3 class="author-name">DR. NAVEED RAHMANI</h3>
      <p class="author-bio">Dr. Rahmani holds a Master’s in Chemistry and a Master’s in Data Systems and worked as a systems analyst. He later earned a doctorate in Religious Studies and helped found a community center in Ohio.</p>
      <div class="barcode-area" aria-label="Reserved space for barcode"></div>
    </section>

    <section class="spine">
      <span class="spine-text">FAITH: ROAD OF ENDLESS GRACE</span>
      <span class="spine-text spine-author">DR. NAVEED RAHMANI</span>
    </section>

    <section class="front">
      <div class="front-art" role="img" aria-label="Radiant sun glowing through a ring of heavenly clouds under a starry sky"></div>
      <h1 class="front-title">
        <span class="line1">FAITH</span>
        <span class="line2">ROAD OF</span>
        <span class="line3">ENDLESS GRACE</span>
      </h1>
      <p class="front-subtitle">Handbook for Nurturing Calm<br>Hearts and Gentle Living</p>
      <p class="front-author">DR. NAVEED RAHMANI</p>
    </section>
  </div>
</div>
</body>
</html>
```